Mental Health care Company in Washington DC

We are a new mental health care services provider in Washington DC. Please look at these sites.
https://brightwaterfamilysupport.com
https://www.quietharborinc.com
https://willowgate-dc.org/
https://www.tidepathdc.com
https://www.thelanternofdc.com

```html
<!DOCTYPE html>
<html lang="en">
<head>
<meta charset="utf-8">
<title>Lumen Health Services</title>
<link href="https://fonts.googleapis.com/css2?family=Montserrat:wght@400;500;600;700&family=Roboto:wght@400;500;700&display=swap" rel="stylesheet">
<style>
:root{
  --orange:#ee6c1e;
  --navy:#0c1a3c;
  --teal:#8fd0d4;
  --teal-dark:#5fb7bd;
  --mint:#eefafb;
  --text:#4a4f5c;
  --muted:#7a7f8a;
  --white:#ffffff;
  --head:'Montserrat',sans-serif;
  --body:'Roboto',sans-serif;
}
*{box-sizing:border-box;margin:0;padding:0}
html,body{width:1200px;height:4878px;overflow:hidden}
body{position:relative;background:var(--white);font-family:var(--body);color:var(--text)}
.abs{position:absolute}
.btn{position:absolute;display:flex;align-items:center;justify-content:center;gap:8px;background:var(--orange);color:var(--white);font:700 14px var(--body);border-radius:0 28px 0 28px;text-transform:uppercase;letter-spacing:.2px}
.btn .arrow{width:14px;height:14px;border-radius:50%;background:var(--white);display:inline-flex;align-items:center;justify-content:center}
.btn .arrow::after{content:"";border-left:5px solid var(--orange);border-top:3.5px solid transparent;border-bottom:3.5px solid transparent;margin-left:2px}
.photo{position:absolute}

/* header */
.topbar{left:440px;top:0;width:760px;height:53px;background:var(--navy);clip-path:polygon(30px 0,100% 0,100% 100%,0 100%)}
.contact-chip{position:absolute;top:8px;display:flex;gap:10px;align-items:center;color:var(--white)}
.contact-chip .ico{width:34px;height:34px;border:1.5px solid #6a7594;border-radius:4px;display:flex;align-items:center;justify-content:center}
.contact-chip small{display:block;font-size:11px;color:#c8cde0}
.contact-chip b{font-size:13.5px;font-weight:500}
.appt{left:890px;top:8px;width:198px;height:37px;border-radius:0 20px 0 20px;font-size:12.5px}
.logo{position:absolute;display:flex;align-items:center;gap:10px;font:500 26px var(--head);color:var(--navy)}
.logo .dot{width:12px;height:12px;border-radius:50%;background:var(--orange)}
.nav{position:absolute;top:74px;left:418px;display:flex;gap:38px;font:700 13.5px var(--body);color:var(--navy)}
.nav .on{color:var(--orange)}

/* hero */
.hero{left:0;top:113px;width:1200px;height:720px;background:linear-gradient(180deg,#c7cfd3 0%,#d8d2c8 35%,#b5a08c 60%,#9f8a78 100%)}
.hero h1{position:absolute;left:110px;top:125px;font:700 46px/1.2 var(--head);color:var(--navy)}
.hero h1 span{font-weight:400}
.hero p{position:absolute;left:112px;top:260px;width:520px;font:500 16.5px/27px var(--body);color:#111}
.hero-wave{position:absolute;left:0;top:520px}

/* section titles */
.sec-title{position:absolute;left:0;width:1200px;text-align:center;font:700 42px var(--head);color:var(--navy)}
.sec-title span{font-weight:400}

/* about */
.about-art{left:110px;top:833px;width:470px;height:470px;border-radius:40px;background:linear-gradient(135deg,#f0a36d 0%,#f4c7a3 45%,#8fd0d4 55%,#5fb7bd 100%)}
.about h2{position:absolute;left:659px;top:880px;font:700 38px var(--head);color:var(--navy)}
.about h2 span{font-weight:400}
.about p{position:absolute;left:660px;width:430px;font:400 14px/26px var(--body);color:var(--text)}

/* services */
.services{left:0;top:1397px;width:1200px;height:800px;background:var(--mint)}
.card{position:absolute;top:1590px;width:306px;height:445px;background:var(--white);border-radius:10px;box-shadow:0 6px 18px rgba(12,26,60,.18)}
.card .img{position:absolute;left:8px;top:8px;width:290px;height:215px}
.card .badge{position:absolute;left:117px;top:190px;width:72px;height:72px;border-radius:50%;background:var(--teal);border:4px solid var(--white)}
.card h3{position:absolute;top:268px;width:100%;text-align:center;font:500 19px var(--body);color:#111}
.card p{position:absolute;top:308px;left:18px;width:270px;text-align:center;font:400 14px/22px var(--body);color:var(--muted)}
.card .btn{left:74px;top:386px;width:159px;height:42px;border-radius:0 22px 0 22px;font-size:13.5px}
.chev{position:absolute;width:20px;height:32px}

/* consultation */
.consult{left:0;top:2195px;width:1200px;height:437px;background:var(--teal)}
.consult h2{position:absolute;top:115px;width:100%;text-align:center;font:700 34px/48px var(--head);color:var(--navy)}
.consult h2 span{font-weight:400;display:block}
.consult p{position:absolute;top:224px;left:170px;width:860px;text-align:center;font:400 14.5px/26px var(--body);color:#1c2334}
.call-btn{position:absolute;left:454px;top:309px;width:290px;height:50px;border-radius:25px;background:var(--orange);border:3px solid var(--white);display:flex;align-items:center;gap:14px;padding-left:6px;color:var(--white);font:700 13px var(--body);text-transform:uppercase}
.call-btn .c{width:34px;height:34px;border-radius:50%;background:var(--white);display:flex;align-items:center;justify-content:center}

/* why */
.why h2{position:absolute;left:110px;top:2785px;font:700 38px var(--head);color:var(--navy)}
.why h2 span{font-weight:400}
.why p{position:absolute;left:110px;width:470px;font:400 14px/26.5px var(--body);color:var(--text)}
.why-frame{left:820px;top:2880px;width:285px;height:256px;background:var(--teal)}
.why-photo{left:647px;top:2716px;width:443px;height:404px;background:linear-gradient(160deg,#8b8e92 0%,#b9b4ad 50%,#5d6f86 100%)}

/* reviews */
.reviews{left:0;top:3270px;width:1200px;height:506px;background:var(--orange)}
.reviews .sec-title{top:102px;color:var(--white)}
.review{position:absolute;top:198px;width:407px;height:230px;background:var(--white);border-radius:36px}
.review .avatar{position:absolute;left:-52px;top:58px;width:114px;height:114px;border-radius:50%;background:linear-gradient(160deg,#6f7e96,#3d4a62);border:4px solid var(--white)}
.review .q{position:absolute;left:100px;top:18px;font:700 60px var(--head);color:#f4a26c;line-height:1}
.review p{position:absolute;left:100px;top:80px;width:290px;font:400 13.5px/24px var(--body);color:var(--muted)}
.review h4{position:absolute;left:100px;top:163px;font:500 16px var(--body);color:#111}
.review .stars{position:absolute;left:100px;top:188px;color:#f4a100;font-size:15px;letter-spacing:3px}

/* contact */
.contact-title{top:3868px}
.col-head{position:absolute;top:3967px;font:500 20px var(--body);color:#111}
.detail{position:absolute;left:110px;display:flex;gap:30px}
.detail b{display:block;font:700 14px var(--body);color:#111;margin-bottom:6px}
.detail span{font:400 14.5px var(--body);color:var(--text)}
.social{position:absolute;top:4255px;width:32px;height:32px;border-radius:50%;background:var(--teal)}
.field{position:absolute;height:43px;border:1px solid #d5d8de;background:#f5f6f8;font:400 11.5px var(--body);color:#777;padding:15px 16px}
.submit{left:560px;top:4259px;width:129px;height:42px;border-radius:0 22px 0 22px}

/* footer */
.footer{left:0;top:4500px;width:1200px;height:378px;background:var(--navy)}
.fcol{position:absolute;top:4578px;color:var(--white)}
.fcol h5{font:500 15.5px var(--body);margin-bottom:28px}
.fcol ul{list-style:none;font:400 13px/28px var(--body);color:#d5d9e4}
.fcol .ci{display:flex;gap:12px;margin-bottom:12px;font-size:13px;line-height:19px;color:#d5d9e4}
.fcol .ci b{display:block;color:var(--white);font-weight:700;font-size:11.5px}
.fsocial{position:absolute;top:4722px;width:32px;height:32px;border-radius:50%;border:1.5px solid var(--white)}
.copy{position:absolute;top:4834px;width:1200px;text-align:center;font:400 14px var(--body);color:#d5d9e4}
.totop{position:absolute;left:1106px;top:4791px;width:36px;height:36px;border-radius:50%;background:var(--orange);display:flex;align-items:center;justify-content:center}
</style>
</head>
<body>

<!-- header -->
<header>
  <div class="abs topbar"></div>
  <div class="contact-chip" style="left:470px">
    <div class="ico"><svg width="18" height="14" viewBox="0 0 18 14"><rect x="1" y="1" width="16" height="12" fill="none" stroke="#fff" stroke-width="1.5"/><path d="M1 1l8 7 8-7" fill="none" stroke="#fff" stroke-width="1.5"/></svg></div>
    <div><small>Email Address</small><b>info@lumenhealthdc.com</b></div>
  </div>
  <div class="contact-chip" style="left:681px">
    <div class="ico"><svg width="16" height="16" viewBox="0 0 24 24"><path d="M6.6 10.8a15 15 0 006.6 6.6l2.2-2.2c.3-.3.7-.4 1-.2 1.1.4 2.3.6 3.6.6.6 0 1 .4 1 1V20c0 .6-.4 1-1 1A17 17 0 013 4c0-.6.4-1 1-1h3.5c.6 0 1 .4 1 1 0 1.3.2 2.5.6 3.6.1.3 0 .7-.2 1z" fill="#fff"/></svg></div>
    <div><small>Call or text us</small><b style="font-size:16px">+1 202 555 0148</b></div>
  </div>
  <div class="btn appt">Make an Appointment</div>
  <div class="logo" style="left:110px;top:30px"><span class="dot"></span>Lumen Health Services</div>
  <nav class="nav"><span class="on">HOME</span><span>ABOUT US</span><span>OUR SERVICES</span><span>OUR TEAM</span><span>RESOURCES</span><span>CONTACT US</span></nav>
</header>

<!-- hero -->
<section class="abs hero">
  <div class="photo" role="img" aria-label="Family smiling together on a beach, a child on a father's shoulders" style="inset:0;background:linear-gradient(100deg,rgba(220,224,226,.7) 0%,rgba(200,196,188,.2) 45%,rgba(80,60,50,.35) 75%,rgba(60,50,45,.3) 100%)"></div>
  <h1>Empowering Minds.<br><span>Healing Together.</span></h1>
  <p>Providing compassionate, evidence-based mental health care to individuals and families across Washington DC.</p>
  <div class="btn" style="left:113px;top:343px;width:205px;height:52px">Get Started <span class="arrow"></span></div>
  <svg class="hero-wave" width="1200" height="200" viewBox="0 0 1200 200" preserveAspectRatio="none">
    <path d="M0 200V130C150 40 300 110 420 140 600 185 760 90 930 90 1060 90 1140 40 1200 0V200Z" fill="#8fd0d4"/>
    <path d="M0 200V140C150 60 300 120 420 148 600 190 760 110 930 110 1060 110 1140 70 1200 30V200Z" fill="#fff"/>
  </svg>
</section>

<!-- about -->
<section class="about">
  <div class="photo about-art" role="img" aria-label="Collage of calm portraits of people in orange and teal tones"></div>
  <h2>About <span>Us</span></h2>
  <p style="top:958px">We are a trusted mental health care provider serving the Washington DC community with a focus on dignity, inclusivity, and healing. Whether you're seeking support for yourself, a loved one, or your child, our licensed clinicians are here to guide your path toward wellness.</p>
  <p style="top:1102px">Sed ut perspiciatis unde omnis iste natus error sit voluptatem aca quae ab architecto beatae vitae dicta sunt explicabo.</p>
  <div class="btn" style="left:660px;top:1196px;width:185px;height:50px">Learn More <span class="arrow"></span></div>
</section>

<!-- services -->
<section class="abs services"></section>
<h2 class="sec-title" style="top:1492px">Our <span>Services</span></h2>
<svg class="chev" style="left:46px;top:1786px" viewBox="0 0 20 32"><path d="M16 2L4 16l12 14" fill="none" stroke="#7a7f8a" stroke-width="3"/></svg>
<svg class="chev" style="left:1134px;top:1786px" viewBox="0 0 20 32"><path d="M4 2l12 14L4 30" fill="none" stroke="#7a7f8a" stroke-width="3"/></svg>
<article class="card" style="left:114px">
  <div class="photo img" role="img" aria-label="Therapist talking with a client" style="background:linear-gradient(135deg,#9aa5b0,#d8cfc2 55%,#6f7f8f)"></div>
  <span class="badge"></span>
  <h3>Individual Therapy</h3>
  <p>Sed ut perspiciatis unde omnis iste natus sit voluptatem accusantium doloremque laudantium, totam rem aperiam,</p>
  <div class="btn">Read More <span class="arrow"></span></div>
</article>
<article class="card" style="left:447px">
  <div class="photo img" role="img" aria-label="Group session with families seated in a circle" style="background:linear-gradient(135deg,#a4a99f,#d9d4cb 50%,#7d8079)"></div>
  <span class="badge"></span>
  <h3>Family &amp; Couples Therapy</h3>
  <p>Sed ut perspiciatis unde omnis iste natus sit voluptatem accusantium doloremque laudantium, totam rem aperiam,</p>
  <div class="btn">Read More <span class="arrow"></span></div>
</article>
<article class="card" style="left:781px">
  <div class="photo img" role="img" aria-label="Counselor with a group of children" style="background:linear-gradient(135deg,#b19a86,#d8c3b2 50%,#7b6a5e)"></div>
  <span class="badge"></span>
  <h3>Child &amp; Adolescent Therapy</h3>
  <p>Sed ut perspiciatis unde omnis iste natus sit voluptatem accusantium doloremque laudantium, totam rem aperiam,</p>
  <div class="btn">Read More <span class="arrow"></span></div>
</article>

<!-- consultation -->
<svg class="abs" style="left:0;top:2150px" width="1200" height="70" viewBox="0 0 1200 70" preserveAspectRatio="none">
  <path d="M0 70V40C200 0 400 10 600 30 800 50 1000 30 1200 0V70Z" fill="#0c1a3c"/>
  <path d="M0 70V62C200 25 400 30 600 48 800 66 1000 50 1200 22V70Z" fill="#8fd0d4"/>
</svg>
<section class="abs consult">
  <h2>Schedule Your Free Consultation And Let’s<span>See What We Can Create Together!</span></h2>
  <p>Sed ut perspiciatis unde omnis iste natus error sit voluptatem accusantium doloremque laudantium, totam rem aperiam, eaque ipsa quae ab illo inventore veritatis et quasi architecto beatae vitae dicta sunt explicabo.</p>
  <div class="call-btn"><span class="c"><svg width="16" height="16" viewBox="0 0 24 24"><path d="M6.6 10.8a15 15 0 006.6 6.6l2.2-2.2c.3-.3.7-.4 1-.2 1.1.4 2.3.6 3.6.6.6 0 1 .4 1 1V20c0 .6-.4 1-1 1A17 17 0 013 4c0-.6.4-1 1-1h3.5c.6 0 1 .4 1 1 0 1.3.2 2.5.6 3.6.1.3 0 .7-.2 1z" fill="#0c1a3c"/></svg></span>Book Their Free Consultation</div>
</section>

<!-- why choose -->
<section class="why">
  <h2>Why Choose <span>Us?</span></h2>
  <p style="top:2852px">Lorem ipsum dolor sit amet, consectetur adipiscing elit, sed do eiusmod tempor incididunt ut labore et dolore magna aliqua. Ut enim ad minim veniam, quis nostrud exercitation ullamco laboris nisi ut aliquip ex ea commodo consequat.</p>
  <p style="top:2970px">Excepteur sint occaecat cupidatat non proident, sunt in culpa qui officia deserunt mollit anim id est laborum.</p>
  <div class="btn" style="left:110px;top:3055px;width:183px;height:50px">Learn More <span class="arrow"></span></div>
  <div class="abs why-frame"></div>
  <div class="photo why-photo" role="img" aria-label="Caregiver comforting an older man at home"></div>
</section>

<!-- reviews -->
<svg class="abs" style="left:0;top:3225px" width="1200" height="60" viewBox="0 0 1200 60" preserveAspectRatio="none">
  <path d="M0 60V30C200 0 420 5 600 25 800 45 1000 30 1200 5V60Z" fill="#0c1a3c"/>
  <path d="M0 60V55C200 25 420 28 600 45 800 60 1000 50 1200 30V60Z" fill="#ee6c1e"/>
</svg>
<section class="abs reviews">
  <h2 class="sec-title">Customer <span>Reviews</span></h2>
  <svg class="chev" style="left:40px;top:297px" viewBox="0 0 20 32"><path d="M16 2L4 16l12 14" fill="none" stroke="#fff" stroke-width="3.5"/></svg>
  <svg class="chev" style="left:1136px;top:297px" viewBox="0 0 20 32"><path d="M4 2l12 14L4 30" fill="none" stroke="#fff" stroke-width="3.5"/></svg>
  <div class="review" style="left:168px">
    <div class="avatar" role="img" aria-label="Portrait of client"></div>
    <div class="q">“</div>
    <p>Sed ut perspiciatis unde omnis iste natus error sit voluptatem accusantium doloremque laudantium, totam rem aperiam,</p>
    <h4>Marcus Reed</h4>
    <div class="stars">★★★★★</div>
  </div>
  <div class="review" style="left:678px">
    <div class="avatar" role="img" aria-label="Portrait of client"></div>
    <div class="q">“</div>
    <p>Sed ut perspiciatis unde omnis iste natus error sit voluptatem accusantium doloremque laudantium, totam rem aperiam,</p>
    <h4>Dana Ellis</h4>
    <div class="stars">★★★★★</div>
  </div>
</section>

<!-- contact -->
<section class="contact">
  <h2 class="sec-title contact-title">contact <span>us</span></h2>
  <h3 class="col-head" style="left:110px">Contact Details</h3>
  <div class="detail" style="top:4035px">
    <svg width="26" height="34" viewBox="0 0 24 32"><path d="M12 1C6 1 2 5.5 2 11c0 8 10 19 10 19s10-11 10-19C22 5.5 18 1 12 1z" fill="#8fd0d4"/><circle cx="12" cy="11" r="4" fill="#fff"/></svg>
    <div><b>ADDRESS</b><span>Linden Row. 214 Linden Row NW, Washington, DC 20005</span></div>
  </div>
  <div class="detail" style="top:4111px">
    <svg width="30" height="30" viewBox="0 0 24 24"><path d="M6.6 10.8a15 15 0 006.6 6.6l2.2-2.2c.3-.3.7-.4 1-.2 1.1.4 2.3.6 3.6.6.6 0 1 .4 1 1V20c0 .6-.4 1-1 1A17 17 0 013 4c0-.6.4-1 1-1h3.5c.6 0 1 .4 1 1 0 1.3.2 2.5.6 3.6.1.3 0 .7-.2 1z" fill="none" stroke="#8fd0d4" stroke-width="1.5"/></svg>
    <div><b>PHONE NUMBER</b><span>+1 202 555 0148</span></div>
  </div>
  <div class="detail" style="top:4181px">
    <svg width="32" height="26" viewBox="0 0 32 26"><rect x="1" y="1" width="30" height="24" fill="none" stroke="#8fd0d4" stroke-width="1.5"/><path d="M1 1l15 13L31 1M1 25l11-10M31 25L20 15" fill="none" stroke="#8fd0d4" stroke-width="1.5"/></svg>
    <div><b>EMAIL</b><span>info@lumenhealthdc.com</span></div>
  </div>
  <span class="social" style="left:112px" aria-label="Social profile"></span>
  <span class="social" style="left:154px" aria-label="Social profile"></span>
  <span class="social" style="left:196px" aria-label="Social profile"></span>

  <h3 class="col-head" style="left:560px">Get In Touch</h3>
  <div class="field" style="left:560px;top:4028px;width:248px">👤 Name</div>
  <div class="field" style="left:838px;top:4028px;width:250px">✆ Phone Number</div>
  <div class="field" style="left:560px;top:4087px;width:248px">✉ Email Address</div>
  <div class="field" style="left:838px;top:4087px;width:250px">✎ Subject</div>
  <div class="field" style="left:560px;top:4144px;width:527px;height:84px;padding-top:34px">✉ Messagge</div>
  <div class="btn submit">Submit</div>
</section>

<!-- footer -->
<svg class="abs" style="left:0;top:4375px" width="1200" height="140" viewBox="0 0 1200 140" preserveAspectRatio="none">
  <path d="M0 140V100C150 30 300 10 480 50 650 90 800 110 950 80 1060 60 1140 40 1200 30V140Z" fill="#8fd0d4"/>
  <path d="M0 140V135C150 75 300 60 480 90 650 120 820 135 960 105 1070 85 1140 70 1200 62V140Z" fill="#0c1a3c"/>
</svg>
<footer class="abs footer"></footer>
<div class="logo" style="left:120px;top:4642px;color:#fff;font-size:25px"><span class="dot"></span>Lumen Health Services</div>
<span class="fsocial" style="left:181px" aria-label="Social profile"></span>
<span class="fsocial" style="left:224px" aria-label="Social profile"></span>
<span class="fsocial" style="left:267px" aria-label="Social profile"></span>
<div class="fcol" style="left:456px">
  <h5>Quick Links</h5>
  <ul><li>Home</li><li>About Us</li><li>Our Services</li><li>Resources</li><li>Testimonials</li><li>Contact Us</li></ul>
</div>
<div class="fcol" style="left:640px">
  <h5>About Company</h5>
  <ul><li>Legal Information</li><li>Terms &amp; Condition</li><li>Privacy Policy</li><li>Support</li><li>Site Map</li></ul>
</div>
<div class="fcol" style="left:846px;width:250px">
  <h5>Contact Us</h5>
  <div class="ci"><svg width="12" height="12" viewBox="0 0 24 24"><path d="M6.6 10.8a15 15 0 006.6 6.6l2.2-2.2c.3-.3.7-.4 1-.2 1.1.4 2.3.6 3.6.6.6 0 1 .4 1 1V20c0 .6-.4 1-1 1A17 17 0 013 4c0-.6.4-1 1-1h3.5c.6 0 1 .4 1 1 0 1.3.2 2.5.6 3.6.1.3 0 .7-.2 1z" fill="#ee6c1e"/></svg><div><b>Phone</b>+1 (202) 555 0148</div></div>
  <div class="ci"><svg width="13" height="11" viewBox="0 0 32 26"><rect width="32" height="26" fill="#ee6c1e"/><path d="M1 1l15 13L31 1" fill="none" stroke="#0c1a3c" stroke-width="3"/></svg><div><b>Email</b>info@lumenhealthdc.com</div></div>
  <div class="ci"><svg width="11" height="14" viewBox="0 0 24 32"><path d="M12 1C6 1 2 5.5 2 11c0 8 10 19 10 19s10-11 10-19C22 5.5 18 1 12 1z" fill="#ee6c1e"/></svg><div><b>Location</b>Linden Row. 214 Linden Row NW, Washington, DC 20005</div></div>
</div>
<div class="totop"><svg width="14" height="10" viewBox="0 0 14 10"><path d="M1 8l6-6 6 6" fill="none" stroke="#fff" stroke-width="2.2"/></svg></div>
<p class="copy">2025 Copyright - Lumen Health | All Rights Reserved</p>

</body>
</html>
```